Tech business card design

We need an amazing business card design for our new business 'Pexla' a marketing tech startup based in Sydney, Australia. We provide an online marketplace for businesses to search and buy advertising media, connect with service providers and learn more about marketing. We wish to communicate 'cool tech', reliability and professionalism and design based around our logo.

Target Market(s)

Business Owners

Contact Information for Business Card

Name
Position
Email Address
Website
Phone Number

Font styles to use
Other font styles liked:
• Avenir & Avenir Next

Colors

Designer to choose colors to be used in the design.

```html
<!DOCTYPE html>
<html lang="en">
<head>
<meta charset="utf-8">
<title>Pexla Business Card</title>
<link href="https://fonts.googleapis.com/css2?family=Nunito+Sans:wght@400;700;800&display=swap" rel="stylesheet">
<style>
  :root {
    --navy: #180f3c;
    --navy-soft: #2a2160;
    --paper: #f4f4f4;
    --backdrop: #e3e3e3;
    --ink: #180f3c;
    --text: #2a2a3a;
  }
  * { margin: 0; padding: 0; box-sizing: border-box; }
  html, body { width: 1200px; height: 960px; overflow: hidden; }
  body {
    background: var(--backdrop);
    font-family: "Nunito Sans", "Avenir Next", sans-serif;
    position: relative;
  }
  .card {
    position: absolute;
    left: 335px;
    width: 535px;
    height: 327px;
    overflow: hidden;
  }
  .card-front { top: 138px; background: var(--navy); }
  .card-back { top: 509px; background: var(--paper); }

  .circuit-art {
    position: absolute;
    left: 200px;
    top: 0;
    width: 335px;
    height: 327px;
    background: radial-gradient(circle at 75% 45%, var(--navy-soft) 0%, rgba(42,33,96,0.55) 40%, rgba(24,15,60,0) 75%);
  }
  .wordmark {
    position: absolute;
    font-weight: 800;
    letter-spacing: -1px;
    line-height: 1;
  }
  .card-front .wordmark {
    left: 40px;
    top: 252px;
    font-size: 66px;
    color: #ffffff;
  }
  .card-back .wordmark {
    right: 42px;
    top: 32px;
    font-size: 66px;
    color: var(--ink);
  }

  .side-bar {
    position: absolute;
    left: 0;
    top: 0;
    width: 14px;
    height: 327px;
    background: var(--navy);
  }
  .side-notch {
    position: absolute;
    left: 0;
    top: 222px;
  }
  .person {
    position: absolute;
    left: 47px;
    top: 154px;
  }
  .person-name {
    font-size: 21px;
    font-weight: 800;
    color: var(--ink);
    letter-spacing: 0.2px;
    line-height: 24px;
  }
  .person-role {
    font-size: 15px;
    font-weight: 400;
    color: var(--text);
    line-height: 18px;
    letter-spacing: 0.3px;
  }
  .divider {
    position: absolute;
    left: 47px;
    top: 211px;
    width: 32px;
    height: 3px;
    background: var(--navy);
  }
  .contact-list {
    position: absolute;
    left: 47px;
    top: 234px;
    list-style: none;
    font-size: 15px;
    line-height: 18px;
    color: var(--text);
    letter-spacing: 0.2px;
  }
</style>
</head>
<body>
  <section class="card card-front">
    <div class="circuit-art" role="img" aria-label="Faint circuit-board line pattern radiating from a circular core"></div>
    <div class="wordmark">pexla</div>
  </section>

  <section class="card card-back">
    <div class="side-bar"></div>
    <svg class="side-notch" width="30" height="70" viewBox="0 0 30 70" aria-hidden="true">
      <polygon points="0,0 14,0 29,12 29,58 14,70 0,70" fill="var(--navy)"/>
      <rect x="10" y="12" width="7" height="11" rx="1" fill="none" stroke="#fff" stroke-width="1.2"/>
      <rect x="8" y="30" width="11" height="8" fill="none" stroke="#fff" stroke-width="1.2"/>
      <polyline points="8,30 13.5,35 19,30" fill="none" stroke="#fff" stroke-width="1.2"/>
      <circle cx="13.5" cy="51" r="5.5" fill="none" stroke="#fff" stroke-width="1.2"/>
      <ellipse cx="13.5" cy="51" rx="2.3" ry="5.5" fill="none" stroke="#fff" stroke-width="1"/>
      <line x1="8" y1="51" x2="19" y2="51" stroke="#fff" stroke-width="1"/>
    </svg>
    <div class="wordmark">pexla</div>
    <div class="person">
      <div class="person-name">MARCUS REED</div>
      <div class="person-role">FOUNDER, DIRECTOR</div>
    </div>
    <div class="divider"></div>
    <ul class="contact-list">
      <li>+61 (0)400 555 019</li>
      <li>marcus@pexlamedia.com.au</li>
      <li>www.pexlamedia.com.au</li>
    </ul>
  </section>
</body>
</html>
```